Seeking a new website design for electrical contracting company

Brisket & Vane electrical contracting needs a new website for brisket-vane.example

We are looking for modern and something real cool with motion for a landing page. we have some cool images from our photo shoot. maybe even 3d motion our existing logo. we would like something we can edit with news and events and update a past project page. Also allow to take payment
stock images at
https://lorapellwinphotos.picvault-demo.example/Brisket-and-Vane

Target Market(s)

construction , home owners , business owners,

Industry/Entity Type

construction , electrical

Coding

Number of Pages Required

5+ page

Font styles to use
Serif
Sans Serif

Colors
0054AA
0677BA
7BADD7
CADEEF
E8F1F8
0094D4
00A9DD
6FCCEA
C7EBF8
E9F6FB
FFF300
FFF600
FEFA6F
FFFEC7
FFFEE8

Requirements
Must have
• excitement, motion, selling professionalism,

```html
<!DOCTYPE html>
<html lang="en">
<head>
<meta charset="utf-8">
<title>Brisket &amp; Vane — Electrical Contracting</title>
<link href="https://fonts.googleapis.com/css2?family=Poppins:wght@500;600;700&family=Roboto:wght@400;500;700&display=swap" rel="stylesheet">
<style>
:root{
  --navy:#262c6e;
  --navy-deep:#1d2260;
  --orange:#f18a1c;
  --yellow:#f7c51a;
  --text:#555a66;
  --light:#f1f1f1;
  --white:#fff;
}
*{box-sizing:border-box;margin:0;padding:0}
html,body{width:1200px;height:5259px;overflow:hidden}
body{position:relative;font-family:"Roboto",Arial,sans-serif;color:var(--text);background:var(--white)}
section,header,footer{position:absolute;left:0;width:1200px}
.heading{position:absolute;z-index:2;font-family:"Poppins",Arial,sans-serif;font-weight:600;color:var(--navy);text-transform:uppercase;text-align:center;font-size:40px;line-height:50px;letter-spacing:1px;width:1200px;left:0}
.heading span{color:var(--orange)}
.btn{position:absolute;z-index:3;height:50px;padding:0;white-space:nowrap;display:flex;align-items:center;justify-content:center;gap:8px;font-family:"Roboto",sans-serif;font-weight:700;font-size:14px;color:var(--white);text-transform:uppercase;background:linear-gradient(90deg,var(--yellow),var(--orange));clip-path:polygon(8% 0,100% 0,92% 100%,0 100%)}
.btn svg{width:14px;height:14px;flex:none}
.btn-navy{background:var(--navy)}
.photo{position:absolute}

/* header */
.site-header{top:0;height:94px;background:var(--white);z-index:5}
.brand{position:absolute;left:110px;top:22px;display:flex;align-items:center;gap:12px}
.brand-mark{width:38px;height:38px;background:var(--navy)}
.brand-name{font-family:"Poppins",sans-serif;font-weight:600;font-size:25px;color:var(--navy);text-transform:uppercase;letter-spacing:.5px}
.topbar{position:absolute;left:680px;top:0;height:36px;display:flex}
.topbar div{display:flex;align-items:center;gap:8px;color:var(--white);font-size:12px;font-weight:500;white-space:nowrap}
.topbar .mail{background:var(--navy);clip-path:polygon(5% 0,100% 0,95% 100%,0 100%);width:228px;justify-content:center}
.topbar .tel{background:var(--orange);clip-path:polygon(6% 0,100% 0,94% 100%,0 100%);width:180px;justify-content:center;margin-left:-6px}
.nav{position:absolute;right:113px;top:57px;display:flex;gap:24px;font-size:14px;font-weight:500;color:var(--navy);text-transform:uppercase;white-space:nowrap}
.nav .active{color:var(--orange);position:relative}
.nav .active::after{content:"";position:absolute;left:0;right:0;bottom:-8px;height:3px;background:var(--orange)}

/* hero */
.hero{top:94px;height:680px;background:radial-gradient(ellipse at 50% 40%,#2a64c9 0%,#163a91 45%,#0b1d55 100%)}
.hero-title{position:absolute;top:140px;width:1200px;text-align:center;font-family:"Poppins",sans-serif;font-weight:600;color:var(--white);font-size:70px;letter-spacing:2px;text-transform:uppercase;line-height:1}
.hero-sub{position:absolute;top:222px;width:1200px;text-align:center;font-family:"Poppins",sans-serif;font-weight:500;color:var(--white);font-size:34px;letter-spacing:3px;text-transform:uppercase}
.play{position:absolute;left:562px;top:362px;width:76px;height:76px;border-radius:50%;background:rgba(255,255,255,.35);display:flex;align-items:center;justify-content:center}
.play span{width:56px;height:56px;border-radius:50%;background:var(--white);display:flex;align-items:center;justify-content:center}
.slide-arrow{position:absolute;width:40px;height:40px;border-radius:50%;background:rgba(0,0,0,.6);display:flex;align-items:center;justify-content:center}
.edge{position:absolute;left:0;width:1200px}

/* about */
.about{top:774px;height:520px}
.about-photo{left:128px;top:20px;width:420px;height:480px;clip-path:polygon(50% 0,100% 25%,100% 75%,50% 100%,0 75%,0 25%);background:linear-gradient(135deg,#6b6f78 0%,#b7a57a 50%,#e8b62a 100%)}
.about h2{position:absolute;left:652px;top:60px;font-family:"Poppins",sans-serif;font-weight:600;font-size:44px;color:var(--navy);text-transform:uppercase}
.about h2 span{color:var(--orange)}
.about p{position:absolute;left:652px;width:436px;font-size:13px;line-height:26px;text-align:justify}
.call{position:absolute;left:858px;top:398px;display:flex;align-items:center;gap:12px;white-space:nowrap}
.call-icon{width:46px;height:46px;border-radius:50%;background:var(--navy);display:flex;align-items:center;justify-content:center}
.call small{display:block;font-size:12px;color:var(--navy)}
.call strong{font-size:20px;color:var(--navy);font-weight:700}

/* services */
.services{top:1294px;height:740px;background:var(--navy)}
.services .heading{color:var(--white)}
.service{position:absolute;width:230px;font-size:13px;line-height:22px;color:var(--white)}
.service h3{font-size:16px;font-weight:700;margin-bottom:2px}
.service.left{text-align:right}
.svc-icon{position:absolute;width:80px;height:80px;border-radius:50%;background:linear-gradient(135deg,var(--yellow),var(--orange));display:flex;align-items:center;justify-content:center}
.connector{position:absolute;height:2px;background:var(--orange);width:55px}
.services-name{position:absolute;left:440px;top:340px;width:320px;text-align:center;font-family:"Poppins",sans-serif;font-weight:600;font-size:30px;color:var(--white);text-transform:uppercase;line-height:1.2}

/* projects */
.projects{top:2034px;height:720px}
.project-plus{position:absolute;left:580px;top:215px;width:40px;height:40px;border-radius:50%;background:var(--orange);color:var(--white);font-size:26px;display:flex;align-items:center;justify-content:center}

/* reviews */
.reviews{top:2754px;height:540px;background:var(--light)}
.review-card{position:absolute;top:230px;width:425px;height:228px;background:var(--white);box-shadow:0 4px 14px rgba(0,0,0,.12)}
.review-bar{position:absolute;top:230px;width:26px;height:228px;background:var(--orange);clip-path:polygon(60% 0,100% 0,40% 100%,0 100%)}
.avatar{position:absolute;width:120px;height:120px;border-radius:50%;border:6px solid var(--white);box-shadow:0 3px 10px rgba(0,0,0,.2);background:linear-gradient(160deg,#c9ccd3,#6d7384)}
.quote{position:absolute;font-family:"Poppins",sans-serif;font-size:60px;font-weight:700;color:var(--orange);line-height:1}
.review-text{position:absolute;width:290px;font-size:13px;line-height:25px}
.review-name{position:absolute;font-size:16px;font-weight:700;color:#222}
.stars{position:absolute;color:var(--orange);font-size:16px;letter-spacing:2px}
.review-arrow{position:absolute;top:335px}

/* estimates */
.estimates{top:3294px;height:816px;background:var(--orange)}
.estimates .heading{color:var(--white)}
.contact-item{position:absolute;top:270px;display:flex;gap:14px;color:var(--white)}
.contact-item h4{font-size:15px;font-weight:700;text-transform:uppercase}
.contact-item p{font-size:13px;line-height:18px}
.field{position:absolute;background:var(--white);border-radius:3px;font-size:12px;color:#888;padding:14px 20px}

/* news */
.news{top:4110px;height:640px}
.news-card{position:absolute;top:110px;width:310px;height:430px;background:var(--white);box-shadow:0 4px 14px rgba(0,0,0,.12);text-align:center}
.news-photo{height:230px;background:linear-gradient(160deg,#8c96a8,#c8a13a)}
.date-hex{position:absolute;left:110px;top:180px;width:90px;height:100px;background:var(--orange);clip-path:polygon(50% 0,100% 25%,100% 75%,50% 100%,0 75%,0 25%);color:var(--white);font-family:"Poppins",sans-serif;font-weight:600;font-size:20px;line-height:26px;display:flex;flex-direction:column;justify-content:center}
.news-card h3{margin-top:60px;padding:0 30px;font-size:19px;line-height:30px;font-weight:500;color:#222}
.news-card p{margin-top:8px;padding:0 30px;font-size:12px;line-height:22px}
.news-line{position:absolute;left:95px;bottom:22px;width:120px;height:5px;background:var(--orange)}
.news-arrow{position:absolute;top:320px}

/* footer */
.site-footer{top:4750px;height:509px;background:var(--navy);color:var(--white)}
.footer-name{position:absolute;left:110px;top:330px;width:330px;text-align:center;font-family:"Poppins",sans-serif;font-weight:600;font-size:30px;text-transform:uppercase;white-space:nowrap}
.footer-mark{position:absolute;left:245px;top:250px;width:60px;height:60px;background:var(--white)}
.footer-col{position:absolute;top:200px}
.footer-col h4{font-size:15px;font-weight:700;margin-bottom:8px}
.footer-col h4::after{content:"";display:block;width:40px;height:2px;background:var(--orange);margin-top:6px}
.footer-col li{list-style:none;font-size:12px;line-height:27px}
.footer-contact{display:flex;gap:10px;font-size:12px;line-height:17px;margin-bottom:10px}
.footer-contact b{display:block;font-size:11px}
.footer-rule{position:absolute;left:110px;top:430px;width:980px;height:1px;background:rgba(255,255,255,.35)}
.copyright{position:absolute;top:460px;width:1200px;text-align:center;font-size:13px}
.copyright span{color:var(--orange);text-decoration:underline}
.chat{position:absolute;left:1103px;top:383px;width:36px;height:36px;border-radius:50%;background:var(--orange);display:flex;align-items:center;justify-content:center}
</style>
</head>
<body>

<header class="site-header">
  <div class="brand"><span class="brand-mark"></span><span class="brand-name">Brisket &amp; Vane</span></div>
  <div class="topbar">
    <div class="mail"><svg width="13" height="10" viewBox="0 0 13 10"><rect width="13" height="10" fill="#fff"/><path d="M0 0l6.5 5L13 0" stroke="#262c6e" fill="none"/></svg>dale@brisket-vane.example</div>
    <div class="tel"><svg width="12" height="12" viewBox="0 0 24 24"><path fill="#fff" d="M6.6 10.8a15 15 0 0 0 6.6 6.6l2.2-2.2c.3-.3.7-.4 1-.2 1.1.4 2.3.6 3.6.6.6 0 1 .4 1 1V20c0 .6-.4 1-1 1A17 17 0 0 1 3 4c0-.6.4-1 1-1h3.5c.6 0 1 .4 1 1 0 1.3.2 2.5.6 3.6.1.3 0 .7-.2 1z"/></svg>1-555-010-4477</div>
  </div>
  <nav class="nav"><span class="active">Home</span><span>About</span><span>Our Services</span><span>Project</span><span>News</span><span>Contact</span></nav>
</header>

<section class="hero" role="img" aria-label="Glowing blue network of connected points">
  <h1 class="hero-title">Brisket &amp; Vane</h1>
  <div class="hero-sub">Electrical Contracting</div>
  <a class="btn" style="left:494px;top:288px;width:212px">Get Started <svg viewBox="0 0 14 14"><circle cx="7" cy="7" r="7" fill="#fff"/><path d="M5.5 4l3 3-3 3" stroke="#f18a1c" stroke-width="2" fill="none"/></svg></a>
  <div class="play"><span><svg width="18" height="18" viewBox="0 0 18 18"><path d="M4 2l12 7-12 7z" fill="#f18a1c"/></svg></span></div>
  <div class="slide-arrow" style="left:40px;top:274px"><svg width="14" height="14" viewBox="0 0 14 14"><path d="M9 2L4 7l5 5" stroke="#fff" stroke-width="1.6" fill="none"/></svg></div>
  <div class="slide-arrow" style="left:1120px;top:274px"><svg width="14" height="14" viewBox="0 0 14 14"><path d="M5 2l5 5-5 5" stroke="#fff" stroke-width="1.6" fill="none"/></svg></div>
  <svg class="edge" style="top:530px" width="1200" height="150" viewBox="0 0 1200 150" preserveAspectRatio="none"><polygon points="0,90 600,0 1200,90 1200,150 0,150" fill="#f18a1c"/><polygon points="0,128 600,38 1200,128 1200,150 0,150" fill="#fff"/></svg>
</section>

<section class="about">
  <div class="photo about-photo" role="img" aria-label="Electrician in hi-vis vest wiring a panel, framed in a hexagon"></div>
  <h2>About <span>Us</span></h2>
  <p style="top:138px">Lorem ipsum dolor sit amet, consectetur adipiscing elit, sed do eiusmod tempor incididunt ut labore et dolore magna aliqua. Ut enim ad minim veniam, quis nostrud exercitation ullamco laboris nisi ut aliquip ex ea commodo consequat. Duis aute irure dolor in in voluptate velit esse cillum dolore eu fugiat nulla pariatur.</p>
  <p style="top:286px">Sed ut perspiciatis unde omnis iste natus error sit voluptatem accusantium doloremque laudantium, totam rem aperiam, eaque illo architecto beatae vitae dicta sunt explicabo.</p>
  <a class="btn" style="left:652px;top:400px;width:180px;height:46px">Learn More <svg viewBox="0 0 14 14"><circle cx="7" cy="7" r="7" fill="#fff"/><path d="M5.5 4l3 3-3 3" stroke="#f18a1c" stroke-width="2" fill="none"/></svg></a>
  <div class="call"><span class="call-icon"><svg width="22" height="22" viewBox="0 0 24 24"><path fill="#fff" d="M6.6 10.8a15 15 0 0 0 6.6 6.6l2.2-2.2c.3-.3.7-.4 1-.2 1.1.4 2.3.6 3.6.6.6 0 1 .4 1 1V20c0 .6-.4 1-1 1A17 17 0 0 1 3 4c0-.6.4-1 1-1h3.5c.6 0 1 .4 1 1 0 1.3.2 2.5.6 3.6.1.3 0 .7-.2 1z"/></svg></span><div><small>Schedule Now</small><strong>1-555-010-4477</strong></div></div>
</section>

<section class="services">
  <svg class="edge" style="top:0" width="1200" height="140" viewBox="0 0 1200 140" preserveAspectRatio="none"><polygon points="0,0 1200,0 1200,20 600,140 0,20" fill="#fff"/><polygon points="0,20 600,118 1200,20 1200,48 600,140 0,48" fill="#f18a1c"/><polygon points="0,48 600,140 1200,48 1200,40 600,128 0,40" fill="#fff"/></svg>
  <h2 class="heading" style="top:222px">Our Services</h2>

  <div class="service left" style="left:88px;top:296px"><h3>Commercial</h3>Lorem ipsum amet, consectetur adipiscing sed do eiusmod</div>
  <div class="svc-icon" style="left:332px;top:296px"><svg width="40" height="40" viewBox="0 0 40 40" fill="none" stroke="#fff" stroke-width="2"><rect x="10" y="6" width="20" height="30"/><path d="M15 12h3M22 12h3M15 18h3M22 18h3M15 24h3M22 24h3M18 36v-6h4v6"/></svg></div>
  <div class="connector" style="left:414px;top:336px"></div>

  <div class="service left" style="left:88px;top:442px"><h3>Construction</h3>Lorem ipsum amet, consectetur adipiscing sed do eiusmod</div>
  <div class="svc-icon" style="left:332px;top:442px"><svg width="40" height="40" viewBox="0 0 40 40" fill="none" stroke="#fff" stroke-width="2"><path d="M12 36V8M6 36h14M12 10h22M12 10l6-4M30 10v8M28 18h4v4h-4z"/></svg></div>
  <div class="connector" style="left:414px;top:482px"></div>

  <div class="service" style="left:882px;top:296px"><h3>Industrial</h3>Lorem ipsum amet, consectetur adipiscing sed do eiusmod</div>
  <div class="svc-icon" style="left:790px;top:296px"><svg width="40" height="40" viewBox="0 0 40 40" fill="none" stroke="#fff" stroke-width="2"><path d="M6 34V18l8 5v-5l8 5v-5l8 5V8h4v26z"/></svg></div>
  <div class="connector" style="left:733px;top:336px"></div>

  <div class="service" style="left:882px;top:442px"><h3>Residential</h3>Lorem ipsum amet, consectetur adipiscing sed do eiusmod</div>
  <div class="svc-icon" style="left:790px;top:442px"><svg width="40" height="40" viewBox="0 0 40 40" fill="none" stroke="#fff" stroke-width="2"><path d="M6 20L20 8l14 12M10 17v17h20V17M17 34v-8h6v8"/></svg></div>
  <div class="connector" style="left:733px;top:482px"></div>

  <div class="services-name">Brisket<br>&amp; Vane</div>

  <svg class="edge" style="top:640px" width="1200" height="100" viewBox="0 0 1200 100" preserveAspectRatio="none"><polygon points="0,40 600,0 1200,40 1200,100 0,100" fill="#f18a1c"/><polygon points="0,64 600,24 1200,64 1200,100 0,100" fill="#fff"/></svg>
</section>

<section class="projects">
  <h2 class="heading" style="top:26px">Our <span>Projects</span></h2>
  <div class="photo" style="left:110px;top:100px;width:325px;height:237px;background:linear-gradient(150deg,#7b8693,#3c5a45)" role="img" aria-label="Electrician in green gloves working on a breaker panel"></div>
  <div class="photo" style="left:448px;top:100px;width:310px;height:237px;background:linear-gradient(150deg,#d9d9d6,#8f9299)" role="img" aria-label="Two workers in hi-vis vests beside an outdoor unit"></div>
  <div class="project-plus">+</div>
  <div class="photo" style="left:779px;top:100px;width:309px;height:237px;background:linear-gradient(150deg,#b08a5e,#6b4c30)" role="img" aria-label="Electrician on a ladder wiring a timber-framed ceiling"></div>
  <div class="photo" style="left:110px;top:354px;width:325px;height:234px;background:linear-gradient(150deg,#8b8f99,#d7a63a)" role="img" aria-label="Smiling electrician in a yellow hard hat in a plant room"></div>
  <div class="photo" style="left:448px;top:354px;width:310px;height:234px;background:linear-gradient(150deg,#f1efec,#b8b2a8)" role="img" aria-label="Electrician fitting pendant lights in a bright kitchen"></div>
  <div class="photo" style="left:779px;top:354px;width:309px;height:234px;background:linear-gradient(150deg,#6d7480,#2b3856)" role="img" aria-label="Team of electricians working at a switchgear cabinet"></div>
  <a class="btn" style="left:486px;top:622px;width:228px;height:48px">View All Projects <svg viewBox="0 0 14 14"><circle cx="7" cy="7" r="7" fill="#fff"/><path d="M5.5 4l3 3-3 3" stroke="#f18a1c" stroke-width="2" fill="none"/></svg></a>
</section>

<section class="reviews">
  <svg class="edge" style="top:0" width="1200" height="50" viewBox="0 0 1200 50" preserveAspectRatio="none"><polygon points="0,0 600,50 1200,0" fill="#fff"/></svg>
  <h2 class="heading" style="top:150px">Customer <span>Reviews</span></h2>
  <svg class="review-arrow" style="left:48px" width="20" height="34" viewBox="0 0 20 34"><path d="M17 3L4 17l13 14" stroke="#262c6e" stroke-width="4" fill="none"/></svg>
  <svg class="review-arrow" style="left:1132px" width="20" height="34" viewBox="0 0 20 34"><path d="M3 3l13 14L3 31" stroke="#262c6e" stroke-width="4" fill="none"/></svg>

  <div class="review-card" style="left:150px"></div>
  <div class="review-bar" style="left:150px"></div>
  <div class="avatar" style="left:112px;top:284px" role="img" aria-label="Portrait of a customer"></div>
  <div class="quote" style="left:268px;top:252px">&ldquo;</div>
  <p class="review-text" style="left:270px;top:304px">Lorem ipsum sit consectetur adipiscing elit, sed do eiusmod tempor incididunt ut labore et dolore magna aliqua.</p>
  <div class="review-name" style="left:270px;top:390px">Marcus Hale</div>
  <div class="stars" style="left:270px;top:412px">★★★★★</div>

  <div class="review-card" style="left:662px"></div>
  <div class="review-bar" style="left:662px"></div>
  <div class="avatar" style="left:624px;top:284px" role="img" aria-label="Portrait of a customer"></div>
  <div class="quote" style="left:780px;top:252px">&ldquo;</div>
  <p class="review-text" style="left:782px;top:304px">Lorem ipsum sit consectetur adipiscing elit, sed do eiusmod tempor incididunt ut labore et dolore magna aliqua.</p>
  <div class="review-name" style="left:782px;top:390px">Renata Ocampo</div>
  <div class="stars" style="left:782px;top:412px">★★★★★</div>
</section>

<section class="estimates">
  <svg class="edge" style="top:0" width="1200" height="130" viewBox="0 0 1200 130" preserveAspectRatio="none"><polygon points="0,0 1200,0 1200,30 600,110 0,30" fill="#f1f1f1"/><polygon points="0,30 600,90 1200,30 1200,58 600,130 0,58" fill="#262c6e"/></svg>
  <h2 class="heading" style="top:212px">Schedule Free Estimates</h2>
  <div class="contact-item" style="left:225px"><svg width="48" height="48" viewBox="0 0 48 48" fill="none" stroke="#fff" stroke-width="2.2"><path d="M24 40s12-12 12-22a12 12 0 0 0-24 0c0 10 12 22 12 22z"/><circle cx="24" cy="18" r="4"/><path d="M8 40h32"/></svg><div><h4>Location:</h4><p>14 Alder Ridge Rd. Millbrook<br>NH 03000</p></div></div>
  <div class="contact-item" style="left:525px"><svg width="48" height="48" viewBox="0 0 24 24" fill="none" stroke="#fff" stroke-width="1.2"><path d="M6.6 10.8a15 15 0 0 0 6.6 6.6l2.2-2.2c.3-.3.7-.4 1-.2 1.1.4 2.3.6 3.6.6.6 0 1 .4 1 1V20c0 .6-.4 1-1 1A17 17 0 0 1 3 4c0-.6.4-1 1-1h3.5c.6 0 1 .4 1 1 0 1.3.2 2.5.6 3.6.1.3 0 .7-.2 1z"/></svg><div><h4>Phone:</h4><p>1-555-010-4477</p></div></div>
  <div class="contact-item" style="left:735px"><svg width="52" height="48" viewBox="0 0 52 48" fill="none" stroke="#fff" stroke-width="2.2"><rect x="3" y="8" width="46" height="32"/><path d="M3 8l23 18L49 8M3 40l17-16M49 40L32 24"/></svg><div><h4>Email:</h4><p>dale@brisket-vane.example</p></div></div>
  <div class="field" style="left:152px;top:370px;width:430px;height:48px">Name</div>
  <div class="field" style="left:152px;top:435px;width:430px;height:48px">Email Address</div>
  <div class="field" style="left:152px;top:500px;width:430px;height:48px">Phone Number</div>
  <div class="field" style="left:606px;top:370px;width:434px;height:178px">Message</div>
  <a class="btn btn-navy" style="left:494px;top:586px;width:206px;height:50px">Submit Now <svg viewBox="0 0 14 14"><circle cx="7" cy="7" r="7" fill="#fff"/><path d="M5.5 4l3 3-3 3" stroke="#262c6e" stroke-width="2" fill="none"/></svg></a>
  <svg class="edge" style="top:716px" width="1200" height="100" viewBox="0 0 1200 100" preserveAspectRatio="none"><polygon points="0,40 600,0 1200,40 1200,100 0,100" fill="#262c6e"/><polygon points="0,66 600,26 1200,66 1200,100 0,100" fill="#fff"/></svg>
</section>

<section class="news">
  <h2 class="heading" style="top:40px">Latest <span>News</span></h2>
  <svg class="news-arrow" style="left:45px" width="22" height="40" viewBox="0 0 22 40"><path d="M19 2L3 20l16 18" stroke="#262c6e" stroke-width="3" fill="none"/></svg>
  <svg class="news-arrow" style="left:1133px" width="22" height="40" viewBox="0 0 22 40"><path d="M3 2l16 18L3 38" stroke="#262c6e" stroke-width="3" fill="none"/></svg>

  <article class="news-card" style="left:110px">
    <div class="news-photo" role="img" aria-label="Two engineers in hard hats reviewing plans"></div>
    <div class="date-hex">JAN<span>25</span></div>
    <h3>Lorem ipsum dolor sit amet, consect</h3>
    <p>Lorem ipsum dolor sit amet, consect adipiscing elit, sed do</p>
    <span class="news-line"></span>
  </article>
  <article class="news-card" style="left:446px">
    <div class="news-photo" style="background:linear-gradient(160deg,#d8a21c,#6a7c9a)" role="img" aria-label="Gloved hands sorting bundled cables"></div>
    <div class="date-hex">JAN<span>25</span></div>
    <h3>Lorem ipsum dolor sit amet, consect</h3>
    <p>Lorem ipsum dolor sit amet, consect adipiscing elit, sed do</p>
  </article>
  <a class="btn" style="left:494px;top:520px;width:206px;height:50px">Learn More <svg viewBox="0 0 14 14"><circle cx="7" cy="7" r="7" fill="#fff"/><path d="M5.5 4l3 3-3 3" stroke="#f18a1c" stroke-width="2" fill="none"/></svg></a>
  <article class="news-card" style="left:782px">
    <div class="news-photo" style="background:linear-gradient(160deg,#b9bcc2,#4f5d75)" role="img" aria-label="Technician kneeling beside outdoor condenser units"></div>
    <div class="date-hex">JAN<span>25</span></div>
    <h3>Lorem ipsum dolor sit amet, consect</h3>
    <p>Lorem ipsum dolor sit amet, consect adipiscing elit, sed do</p>
    <span class="news-line"></span>
  </article>
</section>

<footer class="site-footer">
  <svg class="edge" style="top:0" width="1200" height="130" viewBox="0 0 1200 130" preserveAspectRatio="none"><polygon points="0,0 1200,0 1200,30 600,100 0,30" fill="#fff"/><polygon points="0,30 600,100 1200,30 1200,60 600,130 0,60" fill="#f18a1c"/><polygon points="0,48 600,118 1200,48 1200,54 600,124 0,54" fill="#fff"/></svg>
  <span class="footer-mark"></span>
  <div class="footer-name">Brisket &amp; Vane</div>
  <div class="footer-col" style="left:492px"><h4>Quick Links</h4><ul><li>Home</li><li>About Us</li><li>Services</li><li>Our Projects</li><li>Contact Us</li></ul></div>
  <div class="footer-col" style="left:661px"><h4>About Company</h4><ul><li>Privacy Policy</li><li>Terms of Service</li><li>Site Map</li><li>Imprint</li><li>Terms And Conditions</li></ul></div>
  <div class="footer-col" style="left:875px"><h4>Contact Us</h4>
    <div class="footer-contact"><svg width="12" height="12" viewBox="0 0 24 24"><path fill="#f18a1c" d="M6.6 10.8a15 15 0 0 0 6.6 6.6l2.2-2.2c.3-.3.7-.4 1-.2 1.1.4 2.3.6 3.6.6.6 0 1 .4 1 1V20c0 .6-.4 1-1 1A17 17 0 0 1 3 4c0-.6.4-1 1-1h3.5c.6 0 1 .4 1 1 0 1.3.2 2.5.6 3.6.1.3 0 .7-.2 1z"/></svg><div><b>Phone</b>1-555-010-4477</div></div>
    <div class="footer-contact"><svg width="12" height="10" viewBox="0 0 13 10"><rect width="13" height="10" fill="#f18a1c"/><path d="M0 0l6.5 5L13 0" stroke="#262c6e" fill="none"/></svg><div><b>Email</b>dale@brisket-vane.example</div></div>
    <div class="footer-contact"><svg width="12" height="14" viewBox="0 0 12 14"><path d="M6 14S0 8 0 6a6 6 0 0 1 12 0c0 2-6 8-6 8z" fill="#f18a1c"/><circle cx="6" cy="6" r="2" fill="#262c6e"/></svg><div><b>Location</b>14 Alder Ridge Rd. Millbrook<br>NH 03000</div></div>
  </div>
  <div class="chat"><svg width="18" height="16" viewBox="0 0 18 16"><path d="M2 1h14a1 1 0 0 1 1 1v9a1 1 0 0 1-1 1H7l-4 3v-3H2a1 1 0 0 1-1-1V2a1 1 0 0 1 1-1z" fill="#fff"/></svg></div>
  <div class="footer-rule"></div>
  <p class="copyright">2025 Copyrights - <span>Brisket &amp; Vane</span> | All Rights Reserved</p>
</footer>

</body>
</html>
```